Business Card design for law firm = Brightvale Australia

We are seeking a new design for our business cards.
We are keeping our logo, which is attached.
We need space for
Name
Title
Address is , which is
Level 7
214 Marlowe Street
Sydney NSW 2047
Phone :
Mobile :
Fax :
Email :
DX :
website www.brightvale-example.com.au

Industry/Entity Type

Law Firm / Banking and Finance

Contact Information for Business Card

We are seeking a new design for our business cards. We are keeping our logo. We need space for Name Title Address is Level 7 214 Marlowe Street Sydney NSW 2047 Phone Mobile Fax Email DX website www.brightvale-example.com.au

Colors
0054AA
0677BA
7BADD7
CADEEF
E8F1F8

Requirements
Must have
• see our website for general feel www.brightvale-example.com.au

```html
<!DOCTYPE html>
<html lang="en">
<head>
<meta charset="utf-8">
<title>Brightvale Business Card</title>
<link rel="stylesheet" href="https://fonts.googleapis.com/css2?family=Crimson+Pro:wght@400&family=Open+Sans:wght@300&display=swap">
<style>
  :root {
    --page: #2b2b2b;
    --front-top: #2f52a0;
    --front-bottom: #2c4a92;
    --accent: #1a8fc6;
    --ink-light: #ecebea;
    --back-top: #f3f3f3;
    --back-bottom: #d9d9d9;
    --name-blue: #2a4a9a;
    --ink-dark: #2a2a2a;
  }
  * { margin: 0; padding: 0; box-sizing: border-box; }
  html, body { width: 1200px; height: 1138px; overflow: hidden; background: var(--page); }
  .canvas { position: relative; width: 1200px; height: 1138px; font-family: "Crimson Pro", Georgia, serif; }
  .card { position: absolute; border-radius: 16px; overflow: hidden; }
  .card-front {
    left: 272px; top: 184px; width: 622px; height: 376px;
    background: linear-gradient(180deg, var(--front-top), var(--front-bottom));
  }
  .brand-name {
    position: absolute; left: 0; right: 0; top: 176px; text-align: center;
    color: var(--ink-light); font-size: 50px; font-weight: 400; line-height: 1;
  }
  .tagline {
    position: absolute; left: 0; right: 0; top: 236px; text-align: center;
    font-family: "Open Sans", Arial, sans-serif; font-weight: 300;
    font-size: 18px; letter-spacing: 1.6px; color: var(--accent);
  }
  .front-url {
    position: absolute; left: 0; right: 0; top: 333px; text-align: center;
    font-size: 15px; letter-spacing: 7.5px; color: var(--ink-light);
  }
  .front-bar { position: absolute; left: 142px; width: 340px; bottom: 0; height: 9px; background: var(--accent); }

  .card-back {
    left: 274px; top: 606px; width: 619px; height: 375px;
    background: linear-gradient(180deg, var(--back-top), var(--back-bottom));
  }
  .person { position: absolute; right: 348px; top: 160px; text-align: right; }
  .person-name { font-size: 24px; color: var(--name-blue); line-height: 1.1; }
  .person-title { font-size: 17px; color: var(--ink-dark); line-height: 1.2; }
  .contacts { position: absolute; left: 292px; top: 146px; list-style: none; }
  .contacts li { display: flex; align-items: center; height: 19.6px; font-size: 16px; color: var(--ink-dark); white-space: nowrap; }
  .contacts svg { width: 14px; height: 14px; fill: var(--accent); margin-right: 18px; flex: none; }
  .address { position: absolute; left: 0; right: 0; top: 320px; text-align: center; font-size: 17px; color: var(--ink-dark); }
</style>
</head>
<body>
<main class="canvas">
  <section class="card card-front">
    <p class="brand-name">Brightvale</p>
    <p class="tagline">strategic legal outsourcing</p>
    <p class="front-url">www.brightvale-example.com.au</p>
    <div class="front-bar"></div>
  </section>

  <section class="card card-back">
    <div class="person">
      <p class="person-name">Daniel Harrow</p>
      <p class="person-title">Managing Director</p>
    </div>
    <ul class="contacts">
      <li><svg viewBox="0 0 14 14" aria-hidden="true"><path d="M1 5c0-2 2-3 6-3s6 1 6 3v1h-3V5H4v1H1zM3 7h8l1 5H2z"/></svg>02 9000 4812</li>
      <li><svg viewBox="0 0 14 14" aria-hidden="true"><path d="M4 1h6v3H4zM1 5h12v6h-2V9H3v2H1zM4 10h6v3H4z"/></svg>02 9000 4813</li>
      <li><svg viewBox="0 0 14 14" aria-hidden="true"><path d="M1 3h12v8H1zM2 4l5 4 5-4v1L7 9 2 5z" fill-rule="evenodd"/></svg>daniel.harrow@brightvale-example.com.au</li>
      <li><svg viewBox="0 0 14 14" aria-hidden="true"><circle cx="7" cy="7" r="6"/><path d="M1 7h12M7 1v12M3 3.5h8M3 10.5h8" stroke="#e6e6e6" stroke-width="0.8" fill="none"/></svg>www.brightvale-example.com.au</li>
    </ul>
    <p class="address">Level 7 214 Marlowe Street Sydney NSW 2047</p>
  </section>
</main>
</body>
</html>
```